MirelaStyle e-commerce website design for shopify platform

I currently have a trendy e-commerce clothing store that is primarily based off of the Southern California Style/Trends. I am looking for a redesign of my shopify template as I don't like my current image. I am looking for a sleek clean design that allows more focus on the products. I like neutral backgrounds and easy to use websites. Should be responsive to mobile devices. I would also like to have some ideas for a slide show picture that notifies customers of free shipping if possible. I do also have a theme template that I purchased through Shopify so one could set the theme up for me and edit it to what I need. My website is mirelastyle.com if you would like to look at the type of products I have. I am also looking to do a logo redesign as well- looking for a more stylish logo that would appeal to an approximate age range of 18-40 year old women. I want to be remembered, something to match the web design.

I like teal/turquoise and grey combos but I don't have to have this as the colors.

Target Market(s)

approx. 18-40

Industry/Entity Type

E-Commerce

Number of Pages Required

2 page

Requirements
Must have
• Menu bar, shopify compatible, easy to access/navigate, responsive to mobile devices, easy product upload
Nice to have
• if able ability to resize pictures all to the same size
Should not have
• not be difficult to navigate both on a reg. computer or mobile device

```html
<!DOCTYPE html>
<html lang="en">
<head>
<meta charset="utf-8">
<title>Mirela Style — Home</title>
<link href="https://fonts.googleapis.com/css2?family=Josefin+Sans:wght@400;600;700&family=Lato:wght@300;400;700&display=swap" rel="stylesheet">
<style>
:root{
  --teal:#35d9dc;
  --teal-dark:#1eb3b5;
  --grey-band:#ececec;
  --card-grey:#eeeeee;
  --ink:#222222;
  --ink-soft:#555555;
  --white:#ffffff;
  --btn-dark:#2a3b3c;
}
*{box-sizing:border-box;margin:0;padding:0}
html,body{width:1200px;height:2830px;overflow:hidden}
body{position:relative;background:var(--white);font-family:'Josefin Sans',sans-serif;color:var(--ink)}
.abs{position:absolute}

/* top bar */
.topbar{top:0;left:0;width:1200px;height:50px;background:#f4f4f4}
.topbar-links{right:100px;top:12px;display:flex;align-items:center;gap:14px;font-family:'Lato',sans-serif;font-size:12px;color:#333}
.topbar-links .sep{color:#999}
.topbar-links .icon{display:inline-block;width:14px;height:14px;background:#333;border-radius:3px;vertical-align:-2px;margin-right:6px}
.login-btn{background:var(--teal);color:var(--white);padding:7px 12px;font-weight:700;font-size:12px}

/* header */
.brand{left:100px;top:80px;font-size:52px;font-weight:700;color:var(--ink);letter-spacing:-1px}
.search{left:742px;top:89px;width:358px;height:43px;border:1px solid #ddd;border-radius:3px;display:flex;align-items:center;justify-content:space-between;padding:0 14px;font-family:'Lato',sans-serif;font-weight:700;font-size:13px}

/* nav */
.main-nav{left:100px;top:166px;width:1000px;height:96px;background:var(--teal);display:flex}
.main-nav a{display:flex;align-items:center;padding:0 22px;color:var(--white);text-decoration:none;font-weight:700;font-size:17px;letter-spacing:.5px;border-right:1px solid rgba(255,255,255,.35)}
.main-nav a.active{background:var(--teal-dark);width:158px;justify-content:center;padding:0}
.main-nav a:last-child{border-right:none}

/* hero */
.band-grey{left:0;top:660px;width:1200px;height:629px;background:var(--grey-band)}
.hero{left:100px;top:262px;width:1000px;height:512px;background:linear-gradient(180deg,#c9c7a9 0%,#a89770 55%,#6e5a3d 100%)}
.hero-arrow{top:455px;width:66px;height:79px;background:#1d1d1d;display:flex;align-items:center;justify-content:center}

.section-title{width:1200px;left:0;text-align:center;font-size:30px;font-weight:600;letter-spacing:.5px}

/* new cards */
.new-card{top:877px;width:310px;height:350px}
.new-card .photo{height:268px}
.new-card .caption{height:82px;background:var(--teal);display:flex;justify-content:space-between;align-items:center;padding:0 12px;color:var(--ink)}
.new-card .name{font-size:17px;font-weight:600}
.new-card .price{font-family:'Lato',sans-serif;font-size:28px;font-weight:400}
.ribbon{position:absolute;top:0;left:0;width:70px;height:70px;overflow:hidden}
.ribbon span{position:absolute;top:16px;left:-26px;width:110px;background:#333;color:#fff;font-size:11px;text-align:center;transform:rotate(-45deg);padding:4px 0}

/* grid cards */
.prod{width:234px;height:447px;background:var(--card-grey)}
.prod .photo{height:321px}
.prod .info{position:relative;padding:28px 18px 0}
.prod .name{color:var(--teal-dark);font-size:18px;font-weight:600}
.prod .price{font-family:'Lato',sans-serif;font-weight:300;font-size:34px;color:#333;margin-top:2px}
.cart-btn{position:absolute;right:14px;top:33px;width:52px;height:52px;background:var(--teal-dark);display:flex;align-items:center;justify-content:center}

.view-more{left:494px;top:2340px;width:212px;height:55px;background:#e6e6e6;display:flex;align-items:center;justify-content:center;font-weight:600;font-size:18px}
.view-more-tip{left:590px;top:2395px;width:0;height:0;border-left:10px solid transparent;border-right:10px solid transparent;border-top:10px solid #e6e6e6}

/* footer */
.footer{left:0;top:2438px;width:1200px;height:285px;background:var(--teal);color:var(--white)}
.fcol{top:0;height:285px}
.fcol h3{font-size:18px;font-weight:700;letter-spacing:.5px}
.divider{top:0;width:2px;height:285px;background:rgba(0,0,0,.06)}
.about-text{font-family:'Lato',sans-serif;font-size:13.5px;line-height:24px;width:270px;margin-top:30px}
.newsletter-lead{font-family:'Lato',sans-serif;font-weight:700;font-size:13px;margin-top:30px}
.email-input{width:292px;height:40px;background:#fff;margin-top:14px;font-family:'Lato',sans-serif;font-size:12px;color:#999;padding:13px 12px}
.signup{display:inline-block;margin-top:22px;background:var(--btn-dark);color:#fff;font-size:13px;font-weight:700;padding:8px 16px}
.follow{position:absolute;right:0;top:34px;background:var(--btn-dark);color:#fff;font-size:11px;font-weight:700;padding:9px 14px}
.tw-badge{width:90px;height:82px;background:#fff;display:flex;align-items:center;justify-content:center;color:var(--ink);font-weight:700;font-size:14px}
.tweet{font-family:'Lato',sans-serif;font-size:12.5px;line-height:22px}

.bottom{left:0;top:2723px;width:1200px;height:107px;background:#f4f4f4;font-family:'Lato',sans-serif;font-size:13px;color:#333}
.pay{display:flex;gap:8px;margin-top:12px}
.pay span{width:42px;height:26px;background:#fff;border:1px solid #ccc;font-size:9px;font-weight:700;display:flex;align-items:center;justify-content:center;color:#333}
.social{display:flex;gap:5px;margin-top:10px}
.social span{width:26px;height:26px;border-radius:50%;background:#9a9a9a}
</style>
</head>
<body>

<div class="abs topbar"></div>
<div class="abs topbar-links">
  <span><i class="icon"></i>Create an account</span><span class="sep">|</span>
  <span>
    <svg width="16" height="14" viewBox="0 0 16 14" style="vertical-align:-2px;margin-right:4px"><path d="M0 1h3l2 8h9l2-6H4" fill="none" stroke="#333" stroke-width="1.6"/><circle cx="6" cy="12" r="1.4" fill="#333"/><circle cx="13" cy="12" r="1.4" fill="#333"/></svg>0 items</span><span class="sep">|</span>
  <span><i class="icon"></i>Check out</span>
  <span class="login-btn">LOG IN</span>
</div>

<div class="abs brand">MirelaStyle</div>
<div class="abs search">SEARCH
  <svg width="18" height="18" viewBox="0 0 18 18"><circle cx="7" cy="7" r="5.5" fill="none" stroke="var(--teal-dark)" stroke-width="2"/><path d="M11 11l6 6" stroke="var(--teal-dark)" stroke-width="2.5"/></svg>
</div>

<nav class="abs main-nav">
  <a class="active">WHAT'S NEW?</a><a>DRESSES</a><a>TOPS</a><a>BOTTOMS/ROMPERS</a><a>ACCESSORIES</a><a>SALE</a><a>A LITTLE ABOUT ME</a>
</nav>

<div class="abs band-grey"></div>
<div class="abs hero" role="img" aria-label="Woman riding a bicycle with a basket through a golden wheat field"></div>
<div class="abs hero-arrow" style="left:100px"><svg width="20" height="36" viewBox="0 0 20 36"><path d="M17 2L3 18l14 16" fill="none" stroke="#fff" stroke-width="2"/></svg></div>
<div class="abs hero-arrow" style="left:1034px"><svg width="20" height="36" viewBox="0 0 20 36"><path d="M3 2l14 16L3 34" fill="none" stroke="#fff" stroke-width="2"/></svg></div>

<h2 class="abs section-title" style="top:812px">WHATS NEW!</h2>

<div class="abs new-card" style="left:100px">
  <div class="photo" role="img" aria-label="Blue patterned bell-sleeve playsuit on a wooden background" style="background:linear-gradient(135deg,#8a6d4f,#2b3f7a 50%,#7a5a8a)"></div>
  <div class="ribbon"><span>NEW</span></div>
  <div class="caption"><span class="name">Kiara Playsuit</span><span class="price">$42.00</span></div>
</div>
<div class="abs new-card" style="left:445px">
  <div class="photo" role="img" aria-label="White halter top on a dress form" style="background:linear-gradient(180deg,#fff,#ececec)"></div>
  <div class="caption"><span class="name">Kiara Playsuit</span><span class="price">$42.00</span></div>
</div>
<div class="abs new-card" style="left:790px">
  <div class="photo" role="img" aria-label="Olive halter dress on a dress form against grey" style="background:linear-gradient(180deg,#6a6a6a,#8f8560)"></div>
  <div class="ribbon"><span>NEW</span></div>
  <div class="caption"><span class="name">Kiara Playsuit</span><span class="price">$42.00</span></div>
</div>

<h2 class="abs section-title" style="top:1330px">SEASONAL MUST HAVES</h2>

<!-- product grid -->
<div class="abs prod" style="left:100px;top:1404px"><div class="photo" role="img" aria-label="Model in white bell-sleeve tunic" style="background:linear-gradient(180deg,#5a6a4a,#e8e4dc)"></div><div class="info"><div class="name">Lily Tunic</div><div class="price">$37.00</div><div class="cart-btn"><svg width="26" height="22" viewBox="0 0 16 14"><path d="M0 1h3l2 8h9l2-6H4" fill="none" stroke="#fff" stroke-width="1.6"/><circle cx="6" cy="12" r="1.4" fill="#fff"/><circle cx="13" cy="12" r="1.4" fill="#fff"/></svg></div></div></div>
<div class="abs prod" style="left:355px;top:1404px"><div class="photo" role="img" aria-label="Floral print romper on a hanger" style="background:linear-gradient(180deg,#cfcfcf,#e8d5d8)"></div><div class="ribbon"><span>NEW</span></div><div class="info"><div class="name">Lily Tunic</div><div class="price">$37.00</div><div class="cart-btn"><svg width="26" height="22" viewBox="0 0 16 14"><path d="M0 1h3l2 8h9l2-6H4" fill="none" stroke="#fff" stroke-width="1.6"/><circle cx="6" cy="12" r="1.4" fill="#fff"/><circle cx="13" cy="12" r="1.4" fill="#fff"/></svg></div></div></div>
<div class="abs prod" style="left:610px;top:1404px"><div class="photo" role="img" aria-label="Model in fitted white dress" style="background:linear-gradient(180deg,#f4f4f4,#e6e2de)"></div><div class="info"><div class="name">Lily Tunic</div><div class="price">$37.00</div><div class="cart-btn"><svg width="26" height="22" viewBox="0 0 16 14"><path d="M0 1h3l2 8h9l2-6H4" fill="none" stroke="#fff" stroke-width="1.6"/><circle cx="6" cy="12" r="1.4" fill="#fff"/><circle cx="13" cy="12" r="1.4" fill="#fff"/></svg></div></div></div>
<div class="abs prod" style="left:866px;top:1404px"><div class="photo" role="img" aria-label="Model in white and navy dip-dye maxi dress" style="background:linear-gradient(180deg,#f2f2f2 60%,#3a4a62)"></div><div class="ribbon"><span>NEW</span></div><div class="info"><div class="name">Lily Tunic</div><div class="price">$37.00</div><div class="cart-btn"><svg width="26" height="22" viewBox="0 0 16 14"><path d="M0 1h3l2 8h9l2-6H4" fill="none" stroke="#fff" stroke-width="1.6"/><circle cx="6" cy="12" r="1.4" fill="#fff"/><circle cx="13" cy="12" r="1.4" fill="#fff"/></svg></div></div></div>

<div class="abs prod" style="left:100px;top:1879px"><div class="photo" role="img" aria-label="Model in cobalt blue top and white jeans outdoors" style="background:linear-gradient(180deg,#8fb8d8,#3a5fb0 55%,#5e8a3e)"></div><div class="info"><div class="name">Lily Tunic</div><div class="price">$37.00</div><div class="cart-btn"><svg width="26" height="22" viewBox="0 0 16 14"><path d="M0 1h3l2 8h9l2-6H4" fill="none" stroke="#fff" stroke-width="1.6"/><circle cx="6" cy="12" r="1.4" fill="#fff"/><circle cx="13" cy="12" r="1.4" fill="#fff"/></svg></div></div></div>
<div class="abs prod" style="left:355px;top:1879px"><div class="photo" role="img" aria-label="Model in coral shift dress" style="background:linear-gradient(180deg,#d8d8d8,#e9a394)"></div><div class="ribbon"><span>NEW</span></div><div class="info"><div class="name">Lily Tunic</div><div class="price">$37.00</div><div class="cart-btn"><svg width="26" height="22" viewBox="0 0 16 14"><path d="M0 1h3l2 8h9l2-6H4" fill="none" stroke="#fff" stroke-width="1.6"/><circle cx="6" cy="12" r="1.4" fill="#fff"/><circle cx="13" cy="12" r="1.4" fill="#fff"/></svg></div></div></div>
<div class="abs prod" style="left:610px;top:1879px"><div class="photo" role="img" aria-label="Blue patterned flared trousers" style="background:linear-gradient(180deg,#bfc4c8,#2d4f6e)"></div><div class="ribbon"><span>NEW</span></div><div class="info"><div class="name">Lily Tunic</div><div class="price">$37.00</div><div class="cart-btn"><svg width="26" height="22" viewBox="0 0 16 14"><path d="M0 1h3l2 8h9l2-6H4" fill="none" stroke="#fff" stroke-width="1.6"/><circle cx="6" cy="12" r="1.4" fill="#fff"/><circle cx="13" cy="12" r="1.4" fill="#fff"/></svg></div></div></div>
<div class="abs prod" style="left:866px;top:1879px"><div class="photo" role="img" aria-label="Model in patterned fringe cami top" style="background:linear-gradient(180deg,#e8e8e8,#5fb8a8 60%,#d9d4cc)"></div><div class="info"><div class="name">Lily Tunic</div><div class="price">$37.00</div><div class="cart-btn"><svg width="26" height="22" viewBox="0 0 16 14"><path d="M0 1h3l2 8h9l2-6H4" fill="none" stroke="#fff" stroke-width="1.6"/><circle cx="6" cy="12" r="1.4" fill="#fff"/><circle cx="13" cy="12" r="1.4" fill="#fff"/></svg></div></div></div>

<div class="abs view-more">VIEW MORE</div>
<div class="abs view-more-tip"></div>

<footer class="abs footer">
  <div class="abs fcol" style="left:106px;top:40px">
    <h3>A LITTLE ABOUT ME...</h3>
    <p class="about-text">My name is Mirela (pronounced Mee-rella with a "J") and I have always loved fashion! In 2004, I moved to LA to pursue my love. I have finally made it a reality by opening my own boutique. We currently carry a variety of different labels and hope to incorporate our own in the near future!</p>
  </div>
  <div class="abs divider" style="left:408px"></div>
  <div class="abs fcol" style="left:452px;top:34px">
    <h3><svg width="40" height="32" viewBox="0 0 40 32" style="vertical-align:-8px;margin-right:10px"><rect x="1" y="1" width="38" height="30" fill="none" stroke="#fff" stroke-width="2.5"/><rect x="6" y="7" width="12" height="10" fill="#fff"/><path d="M22 9h12M22 15h12M6 22h28" stroke="#fff" stroke-width="2.5"/></svg>NEWSLETTER</h3>
    <p class="newsletter-lead">We promise to only send you good things.</p>
    <div class="email-input">Enter Your e-mail ID</div>
    <span class="signup">SIGN UP</span>
  </div>
  <div class="abs divider" style="left:772px"></div>
  <div class="abs fcol" style="left:798px;top:0;width:302px">
    <h3 style="margin-top:42px"><span style="display:inline-block;width:26px;height:26px;background:var(--btn-dark);vertical-align:-6px;margin-right:10px"></span>CHIRPER</h3>
    <span class="follow">FOLLOW US</span>
    <div style="display:flex;gap:14px;margin-top:30px">
      <div class="tw-badge">MirelaStyle</div>
      <div class="tweet" style="font-weight:700;margin-top:20px">Mirela Style<br>@MirelaStyle</div>
    </div>
    <p class="tweet" style="font-weight:700;margin-top:10px">New Kiara Playsuit added today so amazing for this fall! Shop at http://www.mirelastyle.com !</p>
    <p class="tweet" style="margin-top:6px">#fashion... http://picshare.com/p/k3-81mTrQa/</p>
  </div>
</footer>

<div class="abs bottom">
  <div class="abs" style="left:100px;top:30px">Search &nbsp;|&nbsp; About Us &nbsp;|&nbsp; Contact Us</div>
  <div class="abs" style="left:100px;top:68px">© 2014 Mirela Style. All Rights Reserved.</div>
  <div class="abs" style="left:450px;top:28px">Payment methods we accept
    <div class="pay"><span>Amora</span><span>PayNest</span><span>Vexa</span><span>Dovi</span><span>Merica</span></div>
  </div>
  <div class="abs" style="left:794px;top:28px">Connect With Us
    <div class="social"><span></span><span></span><span></span><span></span><span></span><span></span><span></span><span></span></div>
  </div>
</div>

</body>
</html>
```